Robotic Physical Therapy office needs a Grand Opening Flyer

We need a Grand Opening flyer design for a robotic physical therapy office named Kinetic Harbor Wellness. We would like it to have a clean, classy, upscale feeling that gives potential clients a V.I.P. feeling. We would like to use the colors black, gray, and yellow (logo will be uploaded).

Event: Thursday, June 1st, 2023 from 12pm-6pm
location: 58274 Pellham Ave, Bloomfield Hills, MI 48519

Industry/Entity Type

Physical therapy

Font styles to use
Script

Colors

Designer to choose colors to be used in the design.

Requirements
Nice to have
• More of a vip feel for the invite

```html
<!DOCTYPE html>
<html lang="en">
<head>
<meta charset="utf-8">
<title>Kinetic Harbor Wellness – Grand Opening</title>
<link href="https://fonts.googleapis.com/css2?family=Playfair+Display:wght@400;500&family=Montserrat:wght@300;400;600;700&display=swap" rel="stylesheet">
<style>
  :root{
    --page:#f1f1f1;
    --ink:#1c1f2e;
    --ink-deep:#12141f;
    --ink-glow:#2f3446;
    --yellow:#f7d418;
    --white:#ffffff;
    --muted:#c9ccd6;
  }
  *{margin:0;padding:0;box-sizing:border-box}
  html,body{width:691px;height:1200px;overflow:hidden;background:var(--page)}
  .canvas{position:relative;width:691px;height:1200px;display:flex;align-items:center;justify-content:center}
  .flyer{position:relative;width:611px;height:815px;background:var(--ink);overflow:hidden;color:var(--white);font-family:"Montserrat",sans-serif}
  .flyer__backdrop{position:absolute;inset:0;background:
      radial-gradient(ellipse 60% 45% at 50% 62%, var(--ink-glow) 0%, rgba(47,52,70,0) 70%),
      linear-gradient(180deg,var(--ink-deep) 0%,var(--ink) 45%,#232738 70%,var(--ink-deep) 100%)}
  .flyer__topbar{position:absolute;top:0;left:0;right:0;height:8px;background:var(--yellow)}
  .brand{position:absolute;top:52px;left:0;right:0;display:flex;justify-content:center;align-items:center;gap:12px}
  .brand__dot{width:34px;height:34px;border-radius:50%;background:var(--white)}
  .brand__name{font-weight:700;font-size:19px;letter-spacing:.5px;color:var(--white);text-transform:uppercase;line-height:1.1;width:170px}
  .headline{position:absolute;top:150px;left:0;right:0;text-align:center;font-family:"Playfair Display",serif;font-weight:400;line-height:.98;font-size:92px;letter-spacing:1px}
  .headline__grand{color:var(--yellow);display:block}
  .headline__opening{color:var(--white);display:block}
  .service{position:absolute;top:356px;left:50%;transform:translateX(-50%);border:1.5px solid var(--muted);padding:9px 18px;font-size:27px;font-weight:400;letter-spacing:1.5px;color:var(--yellow);white-space:nowrap}
  .date{position:absolute;top:442px;left:84px;right:84px}
  .date__day{font-size:46px;font-weight:300;letter-spacing:1px}
  .date__day span{color:var(--yellow)}
  .date__rule{height:2px;background:var(--muted);margin:14px 0 16px}
  .date__row{display:flex;align-items:center;gap:18px}
  .date__year{font-size:54px;font-weight:600;line-height:1}
  .date__time{background:var(--yellow);color:var(--ink-deep);font-size:26px;font-weight:600;padding:6px 16px}
  .venue{position:absolute;top:700px;left:84px;display:flex;align-items:center;gap:12px;font-size:15px;color:var(--muted);letter-spacing:.3px}
</style>
</head>
<body>
<div class="canvas">
  <article class="flyer">
    <div class="flyer__backdrop" role="img" aria-label="Dim photograph of city office buildings at dusk"></div>
    <div class="flyer__topbar"></div>

    <header class="brand">
      <span class="brand__dot"></span>
      <span class="brand__name">Kinetic Harbor Wellness</span>
    </header>

    <h1 class="headline">
      <span class="headline__grand">GRAND</span>
      <span class="headline__opening">OPENING</span>
    </h1>

    <p class="service">ROBOTIC PHYSICAL THERAPY</p>

    <section class="date">
      <p class="date__day">THURSDAY <span>JUNE 1ST</span></p>
      <div class="date__rule"></div>
      <div class="date__row">
        <span class="date__year">2023</span>
        <span class="date__time">from 12pm-6pm</span>
      </div>
    </section>

    <p class="venue">
      <svg width="18" height="24" viewBox="0 0 18 24" aria-hidden="true">
        <path d="M9 1C4.6 1 1.5 4.2 1.5 8.4 1.5 14 9 23 9 23s7.5-9 7.5-14.6C16.5 4.2 13.4 1 9 1z" fill="none" stroke="#f7d418" stroke-width="1.6"/>
        <circle cx="9" cy="8.5" r="2.8" fill="none" stroke="#f7d418" stroke-width="1.6"/>
      </svg>
      58274 Pellham Ave, Bloomfield Hills, MI 48519
    </p>
  </article>
</div>
</body>
</html>
```